Builder of high-end, expensive tables and other furniture

Build a website that represents what we do. I want a luxury feel that appeals to those who can afford our products. We build very high end tables and other furniture using trees that have fallen or are standing dead. We never cut living trees. Trees are harvested, milled, and kiln dried. Then that lumber is meticulously turned into fine furniture using the best equipment. Our furniture prices range from $1,000-$20,000.

Trying to figure out how to raise my spend.

```html
<!DOCTYPE html>
<html lang="en">
<head>
<meta charset="utf-8">
<title>Fallenwood Tables</title>
<link href="https://fonts.googleapis.com/css2?family=Poppins:wght@500;600;700&family=Roboto:ital,wght@0,400;0,500;0,700;1,400&display=swap" rel="stylesheet">
<style>
:root{
  --orange:#e8703a;
  --blue:#2b69ad;
  --ink:#1d2533;
  --text:#555b66;
  --line:#e6e6e6;
  --white:#ffffff;
}
*{box-sizing:border-box;margin:0;padding:0}
html,body{width:1200px;height:3994px;overflow:hidden}
body{font-family:'Roboto',sans-serif;color:var(--text);background:var(--white);position:relative}
.abs{position:absolute}
h1,h2,h3{font-family:'Poppins',sans-serif;color:var(--ink)}
a{color:inherit;text-decoration:none}

/* top bar */
.topbar{top:0;left:0;width:1200px;height:42px;background:var(--blue);color:var(--white);font-size:13px;font-weight:500}
.topbar .call{left:116px;top:13px;display:flex;gap:6px;align-items:center}
.topbar .mail{right:112px;top:13px;display:flex;gap:6px;align-items:center}

/* header */
.header{top:42px;left:0;width:1200px;height:84px;background:var(--white)}
.brand{left:108px;top:22px;display:flex;align-items:center;gap:10px;font-family:'Poppins',sans-serif;font-size:30px;font-weight:500;color:var(--orange)}
.brand .dot{width:16px;height:16px;border-radius:50%;background:var(--orange)}
.nav{left:484px;top:31px;display:flex;gap:29px;font-size:14px;font-weight:700;color:var(--ink)}
.nav .active{border-bottom:3px solid var(--orange);padding-bottom:6px}
.donate{left:942px;top:20px;width:148px;height:42px;border-radius:21px;background:var(--orange);color:var(--white);font-size:14px;font-weight:700;display:flex;align-items:center;justify-content:center}

/* hero */
.hero{top:126px;left:0;width:1200px;height:600px;background:linear-gradient(100deg,#5a4330 0%,#8b6a4c 35%,#b9a186 60%,#8c7257 85%,#5e4a37 100%)}
.hero-frame{left:112px;top:169px;width:575px;height:258px;border:6px solid var(--white);border-top:none;border-left:none}
.hero-card{left:85px;top:141px;width:577px;height:264px;background:var(--orange);color:var(--white);padding:40px 48px}
.hero-card h1{color:var(--white);font-size:44px;font-weight:700;line-height:1.1;white-space:nowrap}
.hero-card p{font-size:14px;line-height:26px;margin-top:20px;width:460px}
.quote-btn{display:inline-flex;margin-top:20px;width:147px;height:42px;border-radius:21px;background:var(--white);color:var(--orange);font-size:13px;font-weight:700;align-items:center;justify-content:center}
.dots{left:563px;top:532px;display:flex;gap:8px}
.dots span{width:12px;height:12px;border-radius:50%;background:var(--white)}
.dots span:first-child{background:var(--orange)}

/* section titles */
.title{width:1200px;left:0;text-align:center;font-size:35px;font-weight:700;color:var(--ink)}

/* steps */
.steps-svg{left:0;top:860px}
.step-label{width:240px;text-align:center;font-size:15px;font-weight:500;color:var(--ink)}
.step-text{width:210px;text-align:center;font-size:13.5px;line-height:24px;color:var(--text)}
.step-name{font-family:'Poppins',sans-serif;font-weight:600;font-size:19px;fill:var(--ink)}

/* about */
.about{top:1327px;left:0;width:1200px;height:436px;background:var(--blue)}
.about-img{left:0;top:0;width:597px;height:436px;background:linear-gradient(135deg,#d8cdb9 0%,#c98d58 40%,#a7693a 70%,#7e4d2b 100%)}
.about-body{left:654px;top:40px;width:434px;color:var(--white)}
.about-body h2{color:var(--white);font-size:33px;font-weight:700}
.about-body p{font-size:13.5px;line-height:25.5px;text-align:justify;margin-top:10px}
.about-body p+p{margin-top:24px}
.learn{display:inline-flex;gap:8px;align-items:center;margin-top:20px;width:156px;height:42px;border-radius:21px;background:var(--orange);font-size:13px;font-weight:700;justify-content:center}

/* products */
.products{top:1908px;left:110px;display:flex;gap:16px}
.product{width:235px;height:325px;border:1px solid var(--line);padding:5px;text-align:center}
.product .img{height:142px}
.product h3{font-family:'Roboto',sans-serif;font-size:18.5px;font-weight:500;margin-top:25px}
.product p{font-size:13.5px;line-height:25px;margin-top:10px}
.product .price{color:var(--orange);font-size:18.5px;font-weight:700;margin-top:15px}

/* testimonials */
.testi{top:2318px;left:0;width:1200px;height:504px;background:var(--orange)}
.testi .title{color:var(--white);top:76px}
.bubble{left:248px;top:133px;width:703px;height:192px;background:var(--white);border-radius:34px;padding:26px 28px;text-align:center}
.bubble::after{content:"";position:absolute;left:62px;bottom:-12px;border:12px solid transparent;border-top-color:var(--white);border-bottom:0}
.bubble blockquote{font-style:italic;font-size:13px;line-height:26px;color:var(--text)}
.bubble .who{margin-top:12px;font-size:20px;color:var(--orange);font-weight:500}
.bubble .who small{font-size:13px;color:var(--ink);font-weight:700;margin-left:6px}
.avatar{width:68px;height:68px;border-radius:50%;border:3px solid var(--white);top:348px;background:linear-gradient(160deg,#e7c3a3,#9b6b4d)}

/* blog */
.blog{top:2972px;left:112px;display:flex;gap:40px}
.post{width:299px;text-align:center}
.post .img{height:196px;border-radius:6px;box-shadow:0 2px 8px rgba(0,0,0,.18)}
.post h3{font-size:19px;font-weight:600;line-height:23px;margin:30px 30px 0}
.post .date{color:var(--orange);font-size:15px;margin-top:18px}
.post p{font-size:13.5px;line-height:26px;margin-top:8px;padding:0 20px}
.post .more{display:inline-block;color:var(--orange);font-size:14px;margin-top:18px;text-decoration:underline}
.view-more{left:505px;top:3398px;width:190px;height:48px;border-radius:24px;background:var(--orange);color:var(--white);font-size:14px;font-weight:500;display:flex;align-items:center;justify-content:center}

/* footer */
.footer{top:3532px;left:0;width:1200px;height:462px;background:var(--blue);color:var(--white)}
.subscribe-label{left:266px;top:66px;font-family:'Poppins',sans-serif;font-size:21px;font-weight:700}
.subscribe-form{left:531px;top:56px;display:flex;border:2px solid var(--white)}
.subscribe-form .field{width:243px;height:44px;background:var(--white);color:#777;font-size:13px;padding:14px 12px}
.subscribe-form .go{width:112px;height:44px;background:var(--orange);font-size:14px;font-weight:700;display:flex;align-items:center;justify-content:center}
.f-brand{left:106px;top:172px;display:flex;align-items:center;gap:10px;font-family:'Poppins',sans-serif;font-size:28px;font-weight:500}
.f-brand .dot{width:14px;height:14px;border-radius:50%;background:var(--white)}
.f-about{left:106px;top:236px;width:258px;font-size:13.5px;line-height:26px}
.f-col{top:172px}
.f-col h4{font-family:'Poppins',sans-serif;font-size:17px;font-weight:600}
.f-col h4::after{content:"";display:block;width:34px;height:2px;background:var(--white);margin-top:10px}
.f-col ul{list-style:none;margin-top:22px;font-size:13.5px;line-height:26px}
.f-col li::before{content:"»";margin-right:8px}
.contact-line{display:flex;gap:12px;font-size:13.5px;line-height:26px;margin-top:14px}
.contact-line .ic{width:24px;height:24px;flex:none;background:var(--orange);display:flex;align-items:center;justify-content:center;margin-top:2px}
.copyright{left:0;width:1200px;top:410px;text-align:center;font-size:13px}
</style>
</head>
<body>

<div class="abs topbar">
  <div class="abs call">
    <svg width="12" height="12" viewBox="0 0 24 24" fill="#fff"><path d="M6.6 10.8a15 15 0 0 0 6.6 6.6l2.2-2.2a1 1 0 0 1 1-.25 11.4 11.4 0 0 0 3.6.57 1 1 0 0 1 1 1V20a1 1 0 0 1-1 1A17 17 0 0 1 3 4a1 1 0 0 1 1-1h3.5a1 1 0 0 1 1 1c0 1.25.2 2.45.57 3.57a1 1 0 0 1-.25 1z"/></svg>
    Call us Today : +1 555 014 2290
  </div>
  <div class="abs mail">
    <svg width="12" height="12" viewBox="0 0 24 24" fill="#fff"><path d="M6.6 10.8a15 15 0 0 0 6.6 6.6l2.2-2.2a1 1 0 0 1 1-.25 11.4 11.4 0 0 0 3.6.57 1 1 0 0 1 1 1V20a1 1 0 0 1-1 1A17 17 0 0 1 3 4a1 1 0 0 1 1-1h3.5a1 1 0 0 1 1 1c0 1.25.2 2.45.57 3.57a1 1 0 0 1-.25 1z"/></svg>
    Mail us : hello@fallenwoodtables.com
  </div>
</div>

<header class="abs header">
  <div class="abs brand"><span class="dot"></span>Fallenwood Tables</div>
  <nav class="abs nav">
    <a class="active">HOME</a><a>ABOUT US</a><a>SERVICES</a><a>BLOG</a><a>CONTACT US</a>
  </nav>
  <a class="abs donate">DONATE NOW</a>
</header>

<section class="abs hero" role="img" aria-label="Rustic wooden kitchen with reclaimed plank walls, wooden stairs and bar stools">
  <div class="abs hero-frame"></div>
  <div class="abs hero-card">
    <h1>FALLENWOOD TABLES</h1>
    <p>Lorem ipsum dolor sit amet, consectetur adipiscing elit, sed do eius mod tempor incididunt ut labore et dolore magna aliqua.</p>
    <a class="quote-btn">GET A QUOTE</a>
  </div>
  <div class="abs dots"><span></span><span></span><span></span><span></span></div>
</section>

<h2 class="abs title" style="top:798px">HOW IT WORKS</h2>

<svg class="abs steps-svg" width="1200" height="240" viewBox="0 860 1200 240">
  <g fill="none" stroke="#2b69ad" stroke-width="5">
    <circle cx="355" cy="961" r="86"/>
    <circle cx="597" cy="961" r="86"/>
    <circle cx="837" cy="961" r="86"/>
  </g>
  <g fill="none" stroke="#1d2533" stroke-width="1.5">
    <path d="M355 1050 V1064 C440 1064 455 1030 458 990 C460 965 470 961 505 961"/>
    <path d="M597 1050 V1064 C680 1064 695 1030 698 990 C700 965 710 961 745 961"/>
    <path d="M837 1050 V1064 C920 1064 938 1030 940 990 L941 960"/>
    <path d="M498 955 L506 961 L498 967"/>
    <path d="M738 955 L746 961 L738 967"/>
  </g>
  <g stroke="#1d2533" stroke-width="1.5">
    <line x1="355" y1="1050" x2="355" y2="1083"/>
    <line x1="597" y1="1050" x2="597" y2="1083"/>
    <line x1="837" y1="1050" x2="837" y2="1083"/>
  </g>
  <g fill="#e8703a">
    <circle cx="355" cy="1088" r="5"/>
    <circle cx="597" cy="1088" r="5"/>
    <circle cx="837" cy="1088" r="5"/>
  </g>
  <g fill="none" stroke="#e8703a" stroke-width="2">
    <circle cx="355" cy="936" r="14"/><path d="M345 947 l-6 10 M365 947 l6 10"/>
    <circle cx="597" cy="934" r="13"/><path d="M591 951 h12 M592 956 h10 M597 914 v-6 M580 920 l-5 -4 M614 920 l5 -4"/>
    <circle cx="837" cy="934" r="13"/><circle cx="837" cy="934" r="5"/><path d="M827 954 h20"/>
  </g>
  <text class="step-name" x="355" y="1007" text-anchor="middle">STEP 1</text>
  <text class="step-name" x="597" y="1007" text-anchor="middle">STEP 2</text>
  <text class="step-name" x="837" y="1007" text-anchor="middle">STEP 3</text>
</svg>

<div class="abs step-label" style="left:235px;top:1110px">TREES ARE HARVESTED</div>
<div class="abs step-label" style="left:477px;top:1110px">MILLED</div>
<div class="abs step-label" style="left:717px;top:1110px">KILN DRIED</div>
<p class="abs step-text" style="left:250px;top:1143px">Lorem ipsum dolor sit amet, consectetur adipiscing elit, sed do eiusmod tempor incididunt et dolore magna</p>
<p class="abs step-text" style="left:492px;top:1143px">Lorem ipsum dolor sit amet, consectetur adipiscing elit, sed do eiusmod tempor incididunt et dolore magna</p>
<p class="abs step-text" style="left:732px;top:1143px">Lorem ipsum dolor sit amet, consectetur adipiscing elit, sed do eiusmod tempor incididunt et dolore magna</p>

<section class="abs about">
  <div class="abs about-img" role="img" aria-label="Wooden outdoor dining table with bench and chairs on a timber deck"></div>
  <div class="abs about-body">
    <h2>ABOUT US</h2>
    <p>Lorem ipsum dolor sit amet, consectetur adipiscing elit, sed do eiusmod tempor incididunt ut labore et dolore magna aliqua. Ut enim ad minim veniam, quis nostrud exercitation ullamco laboris nisi ut aliquip ex ea commodo consequat. Duis aute irure dolor in reprehenderit in voluptate velit esse cillum dolore eu fugiat nulla pariatur.</p>
    <p>Excepteur sint occaecat cupidatat non proident, sunt in culpa qui officia deserunt mollit anim id est laborum.</p>
    <a class="learn">LEARN MORE
      <svg width="13" height="13" viewBox="0 0 16 16"><circle cx="8" cy="8" r="8" fill="#fff"/><path d="M6 4.5 9.5 8 6 11.5" stroke="#e8703a" stroke-width="2" fill="none"/></svg>
    </a>
  </div>
</section>

<h2 class="abs title" style="top:1836px">OUR PRODUCTS</h2>
<div class="abs products">
  <article class="product"><div class="img" role="img" aria-label="Dark modern dining room with wooden table" style="background:linear-gradient(135deg,#3b3b3b,#8a6a4a 60%,#c8b59a)"></div><h3>Lorem ipsum dolor</h3><p>Lorem ipsum dolor sit amet, consectetur adipiscing</p><div class="price">$1,000</div></article>
  <article class="product"><div class="img" role="img" aria-label="Wooden sideboard against a concrete wall" style="background:linear-gradient(180deg,#9a9a98 0%,#b4b3b0 55%,#8a5f3e 70%,#6e4a30)"></div><h3>Lorem ipsum dolor</h3><p>Lorem ipsum dolor sit amet, consectetur adipiscing</p><div class="price">$1,000</div></article>
  <article class="product"><div class="img" role="img" aria-label="Wooden outdoor lounge set with coffee table" style="background:linear-gradient(180deg,#7f8f5e 0%,#a9a17c 45%,#b98a5c 75%,#8d6444)"></div><h3>Lorem ipsum dolor</h3><p>Lorem ipsum dolor sit amet, consectetur adipiscing</p><div class="price">$1,000</div></article>
  <article class="product"><div class="img" role="img" aria-label="Bright kitchen with wooden island and stools" style="background:linear-gradient(180deg,#eeeae3 0%,#dad3c7 50%,#a97a52 80%,#7a5538)"></div><h3>Lorem ipsum dolor</h3><p>Lorem ipsum dolor sit amet, consectetur adipiscing</p><div class="price">$1,000</div></article>
</div>

<section class="abs testi">
  <h2 class="abs title">WHAT PEOPLES SAY</h2>
  <div class="abs bubble">
    <blockquote>"Lorem ipsum dolor sit amet, consectetur adipiscing elit, sed do eiusmod tempor incididunt ut labore et dolore magna aliqua. Ut enim ad minim veniam, quis nostrud exercitation ullamco laboris nisi ut aliquip ex ea commodo consequat. Duis aute irure dolor in reprehenderit in voluptate velit esse cillum officia deserunt mollit anim id est laborum."</blockquote>
    <div class="who">John doe<small>Company name</small></div>
  </div>
  <div class="abs avatar" style="left:284px" role="img" aria-label="Customer portrait"></div>
  <div class="abs avatar" style="left:426px" role="img" aria-label="Customer portrait"></div>
  <div class="abs avatar" style="left:567px" role="img" aria-label="Customer portrait"></div>
  <div class="abs avatar" style="left:709px" role="img" aria-label="Customer portrait"></div>
  <div class="abs avatar" style="left:850px" role="img" aria-label="Customer portrait"></div>
</section>

<h2 class="abs title" style="top:2895px">OUR LATEST BLOG</h2>
<div class="abs blog">
  <article class="post"><div class="img" role="img" aria-label="Furniture workshop floor with lumber stacks" style="background:linear-gradient(180deg,#d9dcd8 0%,#bfc3bd 45%,#c9a77d 80%,#a9835e)"></div><h3>Lorem ipsum dolor sit amet</h3><div class="date">Jun 17, 2020</div><p>Lorem ipsum dolor sit amet, consectetur adipiscing elit, sed do eiusmod</p><a class="more">READ MORE ⟶</a></article>
  <article class="post"><div class="img" role="img" aria-label="Live-edge wooden dining table with chairs" style="background:linear-gradient(160deg,#f1efec 0%,#d8d2ca 40%,#9c6a44 65%,#3a2a20)"></div><h3>Lorem ipsum dolor sit amet</h3><div class="date">Jun 12, 2020</div><p>Lorem ipsum dolor sit amet, consectetur adipiscing elit, sed do eiusmod</p><a class="more">READ MORE ⟶</a></article>
  <article class="post"><div class="img" role="img" aria-label="Office with wooden desk and chairs" style="background:linear-gradient(180deg,#ecebe8 0%,#d6d3ce 55%,#8d6b4c 80%,#5b4535)"></div><h3>Lorem ipsum dolor sit amet</h3><div class="date">Jun 10, 2020</div><p>Lorem ipsum dolor sit amet, consectetur adipiscing elit, sed do eiusmod</p><a class="more">READ MORE ⟶</a></article>
</div>
<a class="abs view-more">VIEW MORE BLOG</a>

<footer class="abs footer">
  <div class="abs subscribe-label">Subscribe Newsletter</div>
  <div class="abs subscribe-form"><div class="field">Email Address</div><div class="go">SUBSCRIBE</div></div>

  <div class="abs f-brand"><span class="dot"></span>Fallenwood Tables</div>
  <p class="abs f-about">Lorem ipsum dolor sit amet, cons ecte tur adipiscing elit, sed do eiusmod tem por incididunt ut labore</p>

  <div class="abs f-col" style="left:450px"><h4>Practice Area</h4>
    <ul><li>Privacy policy</li><li>Terms &amp; condition</li><li>Support</li><li>Cookies</li><li>Services</li></ul></div>
  <div class="abs f-col" style="left:655px"><h4>Quick Links</h4>
    <ul><li>Home</li><li>About Us</li><li>Services</li><li>Rates</li><li>Contact us</li></ul></div>
  <div class="abs f-col" style="left:883px;width:240px"><h4>Contact us</h4>
    <div class="contact-line" style="margin-top:18px"><span class="ic"><svg width="11" height="14" viewBox="0 0 12 16"><path d="M6 0a6 6 0 0 1 6 6c0 4.5-6 10-6 10S0 10.5 0 6a6 6 0 0 1 6-6z" fill="#fff"/><circle cx="6" cy="6" r="2.2" fill="#e8703a"/></svg></span><span>123,Lorem ipsum dolor sit consectetur</span></div>
    <div class="contact-line"><span class="ic"><svg width="12" height="12" viewBox="0 0 24 24" fill="#fff"><path d="M6.6 10.8a15 15 0 0 0 6.6 6.6l2.2-2.2a1 1 0 0 1 1-.25 11.4 11.4 0 0 0 3.6.57 1 1 0 0 1 1 1V20a1 1 0 0 1-1 1A17 17 0 0 1 3 4a1 1 0 0 1 1-1h3.5a1 1 0 0 1 1 1c0 1.25.2 2.45.57 3.57a1 1 0 0 1-.25 1z"/></svg></span><span>+1 555 014 2290</span></div>
    <div class="contact-line" style="margin-top:20px"><span class="ic"><svg width="13" height="10" viewBox="0 0 16 12"><rect width="16" height="12" rx="1" fill="#fff"/><path d="M0 1l8 6 8-6" stroke="#e8703a" stroke-width="1.5" fill="none"/></svg></span><span>hello@fallenwoodtables.com</span></div>
  </div>

  <div class="abs copyright">© Copyright 2023 Fallenwood Tables | All Rights Reserved</div>
</footer>

</body>
</html>
```